Corvane Business Cards

Front of business card will have logo, name, address, & telephone number. Back of card will have a list of services provided - Roads, Substation Pads, Temporary Pads, Site Pads, Land Leveling, Powerline Row Cleaning, Land Clearing, Gates, Fencing, Construction Entrances, Excavation, Trenching, Underground Utilities, Directional Boring, Pile Driving. We are a construction company that uses heavy equipment like bulldozers, motor graders/blades, dump trucks, backhoes, hydro axes, & skid loaders. We build roads, pads, & install electric utility lines & waterlines underground. This logo is new. The word "Construction" can be smaller as uploaded 2 example edited logos. We will be using this card design for many employees.
Target Market(s)
Industrial Electric Powerline, Wind Turbine, Solar Panel, & Water Utility companies.
Contact Information for Business Card
Name/Position - Dwayne Halster - Owner
Address: 4875 FM 309
Ostrand, KS 79412
Phone number - (325) 482-5096

```html
<!DOCTYPE html>
<html lang="en">
<head>
<meta charset="utf-8">
<title>Corvane Construction – Business Card</title>
<link href="https://fonts.googleapis.com/css2?family=Arimo:wght@400;700&family=Orbitron:wght@700&display=swap" rel="stylesheet">
<style>
  :root {
    --maroon: #3c111b;
    --paper: #ffffff;
    --ink-grey: #3a3a3a;
    --soft-grey: #6b6b6b;
    --stage: #e9e7e6;
    --rule: rgba(255,255,255,0.35);
  }
  * { box-sizing: border-box; margin: 0; padding: 0; }
  html, body {
    width: 1200px; height: 1200px; overflow: hidden;
    background: var(--stage);
    font-family: "Arimo", Arial, sans-serif;
  }
  .sheet {
    position: relative; width: 1200px; height: 1200px;
    display: flex; flex-direction: column; align-items: center; justify-content: center;
    gap: 64px;
  }
  .card {
    position: relative; width: 760px; height: 434px;
    box-shadow: 0 10px 30px rgba(0,0,0,0.18);
    overflow: hidden;
  }
  /* Back */
  .card-back {
    background: var(--maroon); color: var(--paper);
    border-radius: 70px 0 70px 0;
    display: flex; flex-direction: column; align-items: center; justify-content: center;
    text-align: center;
  }
  .services-intro, .services-summary {
    font-size: 19px; line-height: 1.32; letter-spacing: 0.2px;
  }
  .services-divider {
    width: 330px; height: 1px; background: var(--rule); margin: 12px 0 10px;
  }
  /* Front */
  .card-front {
    background: var(--paper);
    border-radius: 0 70px 0 70px;
  }
  .holder { position: absolute; left: 58px; top: 62px; }
  .holder-name {
    color: var(--maroon); font-weight: 700; font-size: 28px; letter-spacing: 0.5px;
  }
  .holder-role { color: var(--soft-grey); font-size: 17px; margin-top: 2px; }
  .wordmark {
    position: absolute; right: 50px; top: 150px; width: 380px;
    color: var(--maroon); font-weight: 700; text-align: center; line-height: 1;
  }
  .wordmark-name { font-size: 64px; letter-spacing: 2px; }
  .wordmark-sub { font-size: 30px; letter-spacing: 2px; margin-top: 14px; }
  .address {
    position: absolute; left: 58px; bottom: 78px;
    color: var(--ink-grey); font-size: 20px; line-height: 1.3;
  }
  .phone {
    position: absolute; right: 58px; bottom: 52px;
    font-family: "Orbitron", "Arimo", sans-serif; font-weight: 700;
    color: var(--ink-grey); font-size: 30px; letter-spacing: 1px;
  }
</style>
</head>
<body>
  <main class="sheet">
    <section class="card card-back" aria-label="Card back">
      <p class="services-intro">We are a construction company that<br>uses heavy equipment<br>like bulldozers | motor graders/blades<br>dump trucks | backhoes<br>hydro axes &amp; skid loaders.</p>
      <div class="services-divider"></div>
      <p class="services-summary">We build roads, pads install electric<br>utility lines waterlines underground.</p>
    </section>

    <section class="card card-front" aria-label="Card front">
      <div class="holder">
        <p class="holder-name">DWAYNE HALSTER</p>
        <p class="holder-role">Owner</p>
      </div>
      <div class="wordmark">
        <p class="wordmark-name">CORVANE</p>
        <p class="wordmark-sub">CONSTRUCTION</p>
      </div>
      <p class="address">4875 FM 309<br>Ostrand, KS 79412</p>
      <p class="phone">(325) 482-5096</p>
    </section>
  </main>
</body>
</html>
```